Business Card Design - Service Company

Use of the card mainly in living rooms and relations b2b We wish a card with a modern design, blue tones in the background would be a plus The card must be front / back (one side with the logo / the other with the information of contact )

Font styles to use
Serif

Requirements
Must have
• Using the map on the back of the business card Editable format! Photoshop CS2 / Illustrator CS2
Nice to have
• Mivrel Data IT Plein Ouest Commercial Center, 20417 Valmoreno 0491847352 Siret 41873306200018 APE 6203B https://www.fb.com/boutiquetech.mivreldata www.mivrel-data.com

```html
<!DOCTYPE html>
<html lang="fr">
<head>
<meta charset="utf-8">
<title>Mivrel Data IT – Business Card</title>
<link rel="stylesheet" href="https://fonts.googleapis.com/css2?family=Montserrat:wght@400;500;600&display=swap">
<style>
  :root {
    --page-bg: #ecebea;
    --card-grey: #6a6b70;
    --logo-dark: #3d3e42;
    --brand-blue: #2c87c9;
    --frame-grey: #6c6d72;
    --paper-white: #ffffff;
    --ink-white: #ffffff;
  }
  * { margin: 0; padding: 0; box-sizing: border-box; }
  html, body { width: 1200px; height: 831px; overflow: hidden; }
  body {
    background: var(--page-bg);
    font-family: "Montserrat", Arial, sans-serif;
    position: relative;
  }
  .card {
    position: absolute;
    top: 261px;
    width: 540px;
    height: 309px;
    overflow: hidden;
    box-shadow: 0 6px 18px rgba(0,0,0,0.18);
  }
  .card--front { left: 40px; background: var(--card-grey); }
  .card--back  { left: 620px; background: var(--brand-blue); }

  .front-mark {
    position: absolute;
    inset: 0;
    display: flex;
    align-items: center;
    justify-content: center;
    gap: 12px;
  }
  .brand-name {
    font-weight: 600;
    letter-spacing: 0.5px;
    white-space: nowrap;
  }
  .front-mark .brand-name { font-size: 34px; color: var(--logo-dark); }
  .brand-square { width: 16px; height: 16px; flex: none; }
  .front-mark .brand-square { background: var(--logo-dark); }

  .back-panel { position: absolute; inset: 0; }

  .contact-block {
    position: absolute;
    left: 28px;
    top: 26px;
    color: var(--ink-white);
  }
  .holder-name { font-size: 22px; font-weight: 500; letter-spacing: 1px; }
  .holder-title { font-size: 11px; font-weight: 500; letter-spacing: 1px; margin-top: 2px; }
  .address { font-size: 12px; line-height: 1.6; margin-top: 30px; }
  .contact-list { list-style: none; margin-top: 34px; font-size: 12px; }
  .contact-list li { display: flex; align-items: center; gap: 8px; line-height: 22px; white-space: nowrap; }
  .contact-icon {
    width: 14px; height: 14px;
    background: var(--ink-white);
    border-radius: 2px;
    display: flex; align-items: center; justify-content: center;
    flex: none;
  }
  .contact-icon svg { width: 10px; height: 10px; }

  .back-mark {
    position: absolute;
    left: 352px;
    top: 166px;
    display: flex;
    align-items: center;
    gap: 8px;
  }
  .back-mark .brand-name { font-size: 19px; color: var(--brand-blue); }
  .back-mark .brand-square { width: 12px; height: 12px; background: var(--brand-blue); }
</style>
</head>
<body>

<section class="card card--front" aria-label="Card front">
  <div class="front-mark">
    <span class="brand-name">Mivrel Data IT</span>
    <span class="brand-square"></span>
  </div>
</section>

<section class="card card--back" aria-label="Card back">
  <svg class="back-panel" width="540" height="309" viewBox="0 0 540 309">
    <path d="M318,309 C312,200 318,110 348,32 L540,58 L540,309 Z" fill="var(--frame-grey)"/>
    <path d="M332,309 C326,205 332,118 360,44 L540,66 L540,309 Z" fill="var(--paper-white)"/>
  </svg>

  <div class="contact-block">
    <p class="holder-name">YOUR NAME</p>
    <p class="holder-title">YOUR TITLE</p>
    <p class="address">Centre Commercial<br>Plein Ouest, 20417 Valmoreno</p>
    <ul class="contact-list">
      <li>
        <span class="contact-icon"><svg viewBox="0 0 10 10"><path d="M2,1 L4,1 L4.6,3 L3.6,3.8 C4.2,5 5,5.8 6.2,6.4 L7,5.4 L9,6 L9,8 C9,8.6 8.6,9 8,9 C4.2,9 1,5.8 1,2 C1,1.4 1.4,1 2,1 Z" fill="var(--brand-blue)"/></svg></span>
        0491847352
      </li>
      <li>
        <span class="contact-icon"><svg viewBox="0 0 10 10"><rect x="2.5" y="2.5" width="5" height="5" fill="var(--brand-blue)"/></svg></span>
        boutiquetech.mivreldata
      </li>
      <li>
        <span class="contact-icon"><svg viewBox="0 0 10 10"><circle cx="5" cy="5" r="3.6" fill="none" stroke="var(--brand-blue)" stroke-width="1"/><path d="M1.4,5 H8.6 M5,1.4 C3.4,3.5 3.4,6.5 5,8.6 M5,1.4 C6.6,3.5 6.6,6.5 5,8.6" fill="none" stroke="var(--brand-blue)" stroke-width="0.8"/></svg></span>
        www.mivrel-data.com
      </li>
      <li>
        <span class="contact-icon"><svg viewBox="0 0 10 10"><path d="M5,9 C3,6.5 2,5 2,3.8 A3,3 0 0 1 8,3.8 C8,5 7,6.5 5,9 Z" fill="var(--brand-blue)"/><circle cx="5" cy="3.8" r="1.1" fill="var(--ink-white)"/></svg></span>
        Siret 41873306200018, APE 6203B
      </li>
    </ul>
  </div>

  <div class="back-mark">
    <span class="brand-name">Mivrel Data IT</span>
    <span class="brand-square"></span>
  </div>
</section>

</body>
</html>
```